Brightbay Orthodontics business card design

Need a business card design that reflects our re-branding (orthodontic office - braces) and a new partnership with a pediatric dental office. We would like to include "for adults and children" on the card as well so adults know they are welcome to get their braces here as well. Office design is modern and would like business card to reflect a modern type look. Here's the text we would like to be included on the card:

Darren Wolcott, DDS, MSD
5214 West Linden Avenue, Suite 204
Mansfield, TX 76991
555-418-2637
www.brightbayortho.example
info@brightbayortho.example

Can we add the following to the existing designs? Darren Wolcott, DDS, MSD 5214 West Linden Avenue, Suite 204 Mansfield, TX 76991 555-418-2637

Does anyone have any more vertical designs available? Thanks!

Dental

```html
<!DOCTYPE html>
<html lang="en">
<head>
<meta charset="utf-8">
<title>Brightbay Orthodontics — Business Card</title>
<link rel="stylesheet" href="https://fonts.googleapis.com/css2?family=Exo+2:wght@400;500;600;800&display=swap">
<style>
  :root {
    --page-bg: #e9e7e4;
    --card-white: #ffffff;
    --card-black: #000000;
    --ink-dark: #1a1a1a;
    --ink-light: #ffffff;
    --accent-blue: #1f78c1;
    --accent-orange: #f7931e;
    --accent-pink: #ec1a8c;
    --accent-green: #8cc63f;
    --accent-yellow: #f5d90a;
    --logo-disc: #d9dde2;
  }
  * { margin: 0; padding: 0; box-sizing: border-box; }
  html, body { width: 1200px; height: 900px; overflow: hidden; }
  body {
    background: var(--page-bg);
    font-family: "Exo 2", "Arial", sans-serif;
    display: flex; align-items: center; justify-content: center;
  }
  .business-card {
    position: relative;
    width: 1000px; height: 572px;
    background: var(--card-white);
    overflow: hidden;
    box-shadow: 0 10px 30px rgba(0,0,0,.18);
  }
  .card-waves { position: absolute; inset: 0; width: 100%; height: 100%; }
  .tagline {
    position: absolute; top: 50px; right: 92px;
    font-size: 21px; font-weight: 500; color: var(--ink-dark);
    letter-spacing: .3px;
  }
  .brand {
    position: absolute; top: 100px; left: 70px;
    display: flex; align-items: center; gap: 22px;
  }
  .brand-mark {
    width: 86px; height: 86px; border-radius: 50%;
    background: var(--logo-disc);
  }
  .brand-name {
    font-size: 44px; font-weight: 800; line-height: 1.02;
    color: var(--ink-dark);
  }
  .doctor { position: absolute; left: 108px; top: 430px; }
  .doctor-name { font-size: 30px; font-weight: 500; color: var(--accent-blue); }
  .doctor-credentials { font-size: 20px; font-weight: 500; color: var(--ink-light); margin-top: 4px; }
  .contact {
    position: absolute; right: 60px; top: 240px;
    text-align: right; color: var(--ink-light);
    font-size: 20px; font-weight: 500; line-height: 1.45; font-style: normal;
  }
  .contact-address { margin-bottom: 22px; margin-right: 34px; }
  .contact-line { display: flex; justify-content: flex-end; align-items: center; gap: 12px; }
  .contact-line svg { width: 22px; height: 22px; flex: none; }
</style>
</head>
<body>
  <main class="business-card">
    <svg class="card-waves" viewBox="0 0 1000 572" preserveAspectRatio="none" aria-hidden="true">
      <path class="wave-black" d="M0,385 C180,335 330,335 470,272 C620,205 760,165 1000,160 L1000,572 L0,572 Z" fill="var(--card-black)"/>
      <path class="wave-orange" d="M0,296 C170,266 320,256 460,212 C530,190 580,176 640,162 C585,186 535,202 462,232 C320,282 170,294 0,330 Z" fill="var(--accent-orange)"/>
      <path class="wave-pink" d="M0,338 C170,304 330,292 470,244 C560,212 620,198 690,182 C625,210 565,230 472,264 C330,316 170,330 0,372 Z" fill="var(--accent-pink)"/>
      <path class="wave-green" d="M470,238 C600,190 740,112 1000,100 L1000,136 C770,138 620,180 470,238 Z" fill="var(--accent-green)"/>
    </svg>

    <p class="tagline">For Adults and Children</p>

    <div class="brand">
      <span class="brand-mark" aria-hidden="true"></span>
      <span class="brand-name">Brightbay<br>Orthodontics</span>
    </div>

    <div class="doctor">
      <p class="doctor-name">Darren Wolcott</p>
      <p class="doctor-credentials">DDS, MSD</p>
    </div>

    <address class="contact">
      <p class="contact-address">5214 West Linden Avenue,<br>Suite 204 Mansfield,<br>TX 76991</p>
      <p class="contact-line">555-418-2637
        <svg viewBox="0 0 22 22" aria-hidden="true"><rect x="6" y="2" width="10" height="18" rx="2" fill="none" stroke="var(--accent-pink)" stroke-width="2"/><circle cx="11" cy="16.5" r="1.2" fill="var(--accent-pink)"/></svg>
      </p>
      <p class="contact-line">info@brightbayortho.example
        <svg viewBox="0 0 22 22" aria-hidden="true"><rect x="2" y="5" width="18" height="12" fill="var(--accent-green)"/><path d="M2,5 L11,12 L20,5" fill="none" stroke="var(--card-black)" stroke-width="1.5"/></svg>
      </p>
      <p class="contact-line">www.brightbayortho.example
        <svg viewBox="0 0 22 22" aria-hidden="true"><circle cx="11" cy="11" r="9" fill="var(--accent-yellow)"/><path d="M2,11 H20 M11,2 C6,7 6,15 11,20 M11,2 C16,7 16,15 11,20" fill="none" stroke="var(--card-black)" stroke-width="1.3"/></svg>
      </p>
    </address>
  </main>
</body>
</html>
```